Veltrona Pocket Folder

Create a new pocket folder
An Overview / Background of the Business & Services
We would like a new folder to use when making formal presentations
* The Target Market / Audience you are trying to reach
The target audience are commercial businesses that we are selling group insurance products to
* Design Specifics; any preferences or ideas for Style, Colour, Imagery, etc
We wanted to use the Houston, Texas skyline and create something that was simple, yet modern.
* Do you have an existing website or Facebook page were designers can learn more about your company?
Yes, http://www.veltronagroup.example and we are on Linked-In.
Updates
Project Deadline Extended Reason: We have many people who have to agree. We need to get an answer on the form of the ready art we will receive when we select a designer .Thank you. Added Thursday, April 27, 2017
Industry/Entity Type
Business
Look and feel
Each slider illustrates characteristics of the customer's brand and the style your logo design should communicate.

```html
<!DOCTYPE html>
<html lang="en">
<head>
<meta charset="utf-8">
<title>Veltrona Pocket Folder</title>
<link rel="stylesheet" href="https://fonts.googleapis.com/css2?family=Open+Sans:wght@400;600;700&display=swap">
<style>
  :root {
    --page-bg: #e6e6e6;
    --paper: #ffffff;
    --blue-light: #1ba6e4;
    --blue-mid: #0b8fd2;
    --blue-dark: #0a5f9c;
    --band-grey: #5f6266;
    --logo-grey: #55585c;
    --photo-city: #8a8c88;
    --photo-city-dark: #3d4246;
    --photo-interior: #7a6a5a;
    --text-on-blue: #e8f5fc;
  }
  * { box-sizing: border-box; margin: 0; padding: 0; }
  html, body {
    width: 1200px; height: 1200px; overflow: hidden;
    background: var(--page-bg);
    font-family: "Open Sans", Arial, sans-serif;
  }
  .folder-spread {
    position: absolute; left: 40px; top: 226px;
    width: 1120px; height: 747px;
    display: flex;
    box-shadow: 0 8px 24px rgba(0,0,0,0.18);
  }
  .panel {
    position: relative; width: 560px; height: 747px;
    background: var(--paper); overflow: hidden;
  }
  .panel svg { position: absolute; inset: 0; width: 100%; height: 100%; }
  .contact-block {
    position: absolute; left: 40px; bottom: 40px;
    color: var(--text-on-blue); font-size: 12px; line-height: 1.45;
  }
  .contact-block .company { font-weight: 700; font-size: 13px; }
  .contact-block .lines { margin-top: 10px; }
  .contact-block .line { display: flex; align-items: center; gap: 7px; }
  .contact-block .line svg { position: static; width: 10px; height: 10px; }
  .brand {
    position: absolute; left: 0; right: 0; top: 82px;
    display: flex; justify-content: center; align-items: center; gap: 14px;
  }
  .brand-square { width: 48px; height: 48px; background: var(--blue-mid); border-radius: 6px; }
  .brand-name {
    font-weight: 700; font-size: 52px; color: var(--logo-grey); letter-spacing: 0.5px;
  }
  .front-url {
    position: absolute; right: 70px; bottom: 34px;
    color: var(--text-on-blue); font-size: 12px; letter-spacing: 0.3px;
  }
</style>
</head>
<body>
  <div class="folder-spread">
    <section class="panel panel-back">
      <svg viewBox="0 0 560 747" preserveAspectRatio="none">
        <defs>
          <linearGradient id="backBlue" x1="0" y1="0" x2="1" y2="0">
            <stop offset="0" stop-color="var(--blue-light)"/>
            <stop offset="1" stop-color="var(--blue-dark)"/>
          </linearGradient>
          <linearGradient id="backCity" x1="0" y1="0" x2="0" y2="1">
            <stop offset="0" stop-color="#a3a49e"/>
            <stop offset="0.45" stop-color="var(--photo-city)"/>
            <stop offset="1" stop-color="var(--photo-city-dark)"/>
          </linearGradient>
        </defs>
        <rect class="city-photo" role="img" aria-label="Aerial photograph of the Houston city skyline" x="0" y="0" width="560" height="600" fill="url(#backCity)"/>
        <path class="band-edge" d="M0 548 C180 575 380 560 560 470 L560 747 L0 747 Z" fill="var(--band-grey)"/>
        <path class="blue-pocket" d="M0 556 C180 584 380 568 560 480 L560 747 L0 747 Z" fill="url(#backBlue)"/>
      </svg>
      <div class="contact-block">
        <div class="company">Veltrona Corporation</div>
        <div>2450 West Alder Parkway, Suite 410</div>
        <div>Houston, TX 77099</div>
        <div class="lines">
          <div class="line"><svg viewBox="0 0 10 10"><path d="M2 1 L4 1 L5 3 L4 4 Q5 6 6 6 L7 5 L9 6 L9 8 Q8 9 7 9 Q1 8 1 2 Q1 1 2 1 Z" fill="currentColor"/></svg>713-555-0148</div>
          <div class="line"><svg viewBox="0 0 10 10"><rect x="1" y="2" width="8" height="6" fill="currentColor"/><path d="M1 2 L5 5 L9 2" stroke="#0b8fd2" fill="none"/></svg>info@veltronagroup.example</div>
          <div class="line"><svg viewBox="0 0 10 10"><circle cx="5" cy="5" r="4" fill="none" stroke="currentColor"/><path d="M1 5 H9 M5 1 V9" stroke="currentColor"/></svg>www.veltronagroup.example</div>
        </div>
      </div>
    </section>

    <section class="panel panel-front">
      <svg viewBox="0 0 560 747" preserveAspectRatio="none">
        <defs>
          <linearGradient id="frontBlue" x1="0" y1="0" x2="1" y2="0">
            <stop offset="0" stop-color="var(--blue-light)"/>
            <stop offset="1" stop-color="var(--blue-dark)"/>
          </linearGradient>
          <linearGradient id="interior" x1="0" y1="0" x2="1" y2="0">
            <stop offset="0" stop-color="#8fb0c4"/>
            <stop offset="0.4" stop-color="var(--photo-interior)"/>
            <stop offset="1" stop-color="#4a3a30"/>
          </linearGradient>
          <linearGradient id="greyCity" x1="0" y1="0" x2="0" y2="1">
            <stop offset="0" stop-color="#c9c9c9"/>
            <stop offset="1" stop-color="#6c6c6c"/>
          </linearGradient>
        </defs>
        <path class="blue-line" d="M0 165 C180 260 380 330 560 345 L560 352 C380 338 180 270 0 175 Z" fill="var(--blue-mid)"/>
        <path class="interior-photo" role="img" aria-label="Photograph of a modern office interior" d="M0 175 C180 270 380 338 560 352 L560 360 C380 372 180 350 0 290 Z" fill="url(#interior)"/>
        <path class="blue-line-lower" d="M0 290 C180 350 380 372 560 360 L560 366 C380 380 180 358 0 298 Z" fill="var(--blue-mid)"/>
        <path class="city-photo" role="img" aria-label="Black and white photograph of the city skyline" d="M0 298 C180 358 380 380 560 366 L560 520 L0 520 Z" fill="url(#greyCity)"/>
        <path class="band-edge" d="M0 466 C140 505 280 500 560 332 L560 747 L0 747 Z" fill="var(--band-grey)"/>
        <path class="blue-pocket" d="M0 474 C140 514 280 508 560 342 L560 747 L0 747 Z" fill="url(#frontBlue)"/>
      </svg>
      <div class="brand">
        <div class="brand-square"></div>
        <div class="brand-name">Veltrona</div>
      </div>
      <div class="front-url">www.veltronagroup.example</div>
    </section>
  </div>
</body>
</html>
```